Cosmetic Dental Advert For lift in busy CBD

We need a DIRECT RESPONSE advert designed for a cosmetic dentist that is placing adverts into a building lift.

OFFICE PROVIDES BRANDS ACCESS TO REACH HIGH INCOME PROFESSIONALS WITHIN PREMIUM BUSINESS ENVIRONMENTS

We are not advertising a specific clinic so we want people to go to the website that is advertised and ask for the free initial consultation.

You can reduce the amount of words / points to make it simpler to read.

Target Market(s)

Professional at work - seeing advert in a lift or foyer

Industry/Entity Type

Dental

Colors

Designer to choose colors to be used in the design.

Requirements
Must have
• The domain "www.grinvale47.com.au" must be very strong and encourage people to visit / search for it.
• The offer is a ["FREE Initial consultation" with voucher code "grinvale47"]
• The advert must be in Vector format.
• Apply the landing page corner image bottom right
Nice to have
• Provide a Male / Female version
• Emphasize the beautiful smile like in the sample
Should not have
• Must not be busy. This is a direct response so the viewer must get the call to action in 2 seconds

```html
<!DOCTYPE html>
<html lang="en">
<head>
<meta charset="utf-8">
<title>Cosmetic Dentistry Lift Advert</title>
<link rel="stylesheet" href="https://fonts.googleapis.com/css2?family=Lato:wght@100;300;400;700&display=swap">
<style>
  :root {
    --paper: #f4f4f6;
    --paper-edge: #e6e6ea;
    --pink: #e463c3;
    --lavender: #7f86d0;
    --overlap: #8a4fae;
    --violet: #5b3f9e;
    --navy: #2d2f7a;
    --bar: #2b2226;
    --bar-text: #d9a9c4;
    --url: #e2359a;
    --cross: #cfcfd6;
    --photo-top: #c4b2a8;
    --photo-mid: #7b6a64;
    --photo-low: #2a2427;
  }
  * { margin: 0; padding: 0; box-sizing: border-box; }
  html, body { width: 927px; height: 1200px; overflow: hidden; background: var(--paper); }
  .advert {
    position: relative;
    width: 927px;
    height: 1200px;
    overflow: hidden;
    font-family: "Lato", Arial, sans-serif;
    background: linear-gradient(160deg, #fbfbfc 0%, var(--paper) 55%, var(--paper-edge) 100%);
  }
  .decor { position: absolute; left: 0; top: 0; }
  .headline {
    position: absolute;
    left: 248px;
    top: 118px;
    color: var(--violet);
    font-weight: 300;
    font-size: 88px;
    line-height: 80px;
    letter-spacing: -0.5px;
  }
  .headline-key {
    position: absolute;
    left: 418px;
    top: 250px;
    color: #fff;
    font-weight: 100;
    font-size: 240px;
    line-height: 1;
    letter-spacing: -4px;
  }
  .headline-tail {
    position: absolute;
    left: 500px;
    top: 462px;
    width: 380px;
    text-align: center;
    color: var(--violet);
    font-weight: 300;
    font-size: 86px;
    line-height: 80px;
  }
  .voucher {
    position: absolute;
    left: 585px;
    top: 842px;
    width: 220px;
    text-align: center;
    color: var(--navy);
    font-size: 29px;
    font-weight: 400;
    line-height: 1.25;
  }
  .cta-bar {
    position: absolute;
    left: 0;
    top: 1080px;
    width: 590px;
    height: 120px;
    background: var(--bar);
    border-radius: 0 10px 0 0;
    padding: 14px 0 0 48px;
  }
  .cta-lead { color: var(--bar-text); font-size: 33px; font-weight: 300; line-height: 1.15; }
  .cta-lead strong { color: #fff; font-weight: 700; }
  .cta-url { color: var(--url); font-size: 50px; font-weight: 300; letter-spacing: 0.5px; line-height: 1.2; }
  .brand {
    position: absolute;
    left: 625px;
    top: 1104px;
    display: flex;
    align-items: center;
    gap: 12px;
    color: var(--navy);
    font-size: 50px;
    font-weight: 400;
    letter-spacing: -0.5px;
  }
  .brand-dot { width: 18px; height: 18px; border-radius: 50%; background: var(--navy); }
</style>
</head>
<body>
<main class="advert">
  <svg class="decor" width="927" height="1200" viewBox="0 0 927 1200" aria-hidden="true">
    <g class="crosses" stroke="var(--cross)" stroke-width="5">
      <path d="M172 40v36M154 58h36"/>
      <path d="M710 110v40M690 130h40"/>
      <path d="M880 50v64M848 82h64"/>
      <path d="M70 175v60M40 205h60"/>
    </g>
    <circle class="pink-disc" cx="440" cy="190" r="215" fill="var(--pink)"/>
    <circle class="lavender-disc" cx="672" cy="522" r="328" fill="var(--lavender)"/>
    <clipPath id="pinkArea"><circle cx="440" cy="190" r="215"/></clipPath>
    <circle cx="672" cy="522" r="328" fill="var(--overlap)" clip-path="url(#pinkArea)"/>
  </svg>

  <svg class="decor model-photo" width="927" height="1200" viewBox="0 0 927 1200" role="img" aria-label="Photo of a smiling professional woman with long dark hair in a dark blazer, arms crossed">
    <defs>
      <linearGradient id="photoTone" x1="0" y1="0" x2="0" y2="1">
        <stop offset="0" stop-color="var(--photo-top)"/>
        <stop offset="0.4" stop-color="var(--photo-mid)"/>
        <stop offset="0.75" stop-color="var(--photo-low)"/>
        <stop offset="1" stop-color="#231e21"/>
      </linearGradient>
    </defs>
    <path d="M0 1080 L0 700 C10 640 50 610 70 580 C70 480 80 330 110 280 C140 230 190 212 235 212 C290 212 335 240 355 290 C375 350 378 470 390 560 C430 590 500 620 520 680 L520 1080 Z" fill="url(#photoTone)"/>
  </svg>

  <h1>
    <span class="headline">Transform<br>your</span>
    <span class="headline-key">smile</span>
    <span class="headline-tail">with Cosmetic Dentistry</span>
  </h1>

  <p class="voucher">Voucher code<br>“grinvale47”</p>

  <svg class="decor page-corner" width="927" height="1200" viewBox="0 0 927 1200" aria-hidden="true">
    <defs>
      <linearGradient id="curlBack" x1="0" y1="0" x2="1" y2="1">
        <stop offset="0" stop-color="#ffffff"/>
        <stop offset="0.6" stop-color="#e9e9ee"/>
        <stop offset="1" stop-color="#bfbfc8"/>
      </linearGradient>
      <linearGradient id="curlShade" x1="0" y1="0" x2="1" y2="0">
        <stop offset="0" stop-color="#000" stop-opacity="0.18"/>
        <stop offset="1" stop-color="#000" stop-opacity="0"/>
      </linearGradient>
    </defs>
    <path d="M927 820 C 880 900, 800 980, 760 1080 L 927 1080 Z" fill="#fdfdfd"/>
    <path d="M927 820 C 890 900, 815 990, 770 1062 C 830 1000, 880 985, 927 1000 Z" fill="url(#curlBack)"/>
    <path d="M770 1062 C 830 1000, 880 985, 927 1000 L 927 1020 C 880 1005, 830 1020, 770 1062 Z" fill="url(#curlShade)"/>
  </svg>

  <div class="cta-bar">
    <p class="cta-lead">For a <strong>free</strong> initial consultation visit:</p>
    <p class="cta-url">www.grinvale47.com.au</p>
  </div>

  <div class="brand"><span class="brand-dot"></span>MediCrest</div>
</main>
</body>
</html>
```